Professional consulting firm needing a Word document template

I need a Word document template that can be used flexibly for a flyer or brochure of 1 to 3 pages in length. The first page should be designed in a way that it can stand alone as a one-page flyer without a formal cover page. I have attached sample text as a Word document that could be used as the basis for the first 1-2 pages, however I do need three page layouts designed to give flexibility to use as a 3 page booklet. I have attached our brand guidelines, logo, and some stock images that I have previously purchased (they may not all be useful but it gives some options). <br/>The Word document needs to be set up in away that it can easily be edited to accommodate updates to the text, and some variation in the quantity of text on each page. Each page should be able to accommodate a mixture of paragraph text, bullet points, small boxes to call out highlights, one or more images, and some white space to avoid clutter. It should look professional yet engaging and modern.

Font styles to use
Sans Serif

Requirements
Must have
• Must be an editable Microsoft Word document, using the text provided. Must be a layout suitable to use as 1 page, up to 3 pages. Must comply with brand guidelines.

```html
<!DOCTYPE html>
<html lang="en">
<head>
<meta charset="utf-8">
<title>Train Driver Competency Indicator Development Project</title>
<link rel="stylesheet" href="https://fonts.googleapis.com/css2?family=Montserrat:wght@600;700;800&family=Open+Sans:wght@400;600&display=swap">
<style>
  :root {
    --navy: #13283f;
    --navy-deep: #0d1d2f;
    --cyan: #1eb4e6;
    --cyan-light: #dff3fb;
    --paper: #ffffff;
    --ink: #4a5561;
    --backdrop: #e9ebee;
  }
  * { box-sizing: border-box; margin: 0; padding: 0; }
  html, body {
    width: 1200px; height: 902px; overflow: hidden;
    background: var(--backdrop);
    font-family: "Open Sans", Arial, sans-serif;
  }
  .flyer {
    position: absolute; left: 300px; top: 26px;
    width: 600px; height: 850px;
    background: var(--paper);
    box-shadow: 0 4px 18px rgba(0,0,0,.18);
    overflow: hidden;
  }
  .flyer > * { position: absolute; }
  .hero-photo { left: 0; top: 0; width: 600px; height: 215px; }
  .brand {
    left: 34px; top: 150px;
    font-family: "Montserrat", Arial, sans-serif;
    font-weight: 800; font-size: 30px; letter-spacing: 3px;
    color: var(--navy);
    display: flex; align-items: center; gap: 10px;
  }
  .brand-mark { width: 14px; height: 14px; background: var(--cyan); }
  .title-panel { left: 0; top: 205px; width: 360px; height: 140px; }
  .title-block { left: 34px; top: 222px; width: 285px; color: var(--paper); }
  .title {
    font-family: "Montserrat", Arial, sans-serif;
    font-weight: 800; font-size: 17px; line-height: 1.15;
    text-transform: uppercase; letter-spacing: .5px;
  }
  .intro { margin-top: 10px; font-size: 9.5px; line-height: 1.45; }
  .texture { right: 0; top: 215px; width: 250px; height: 150px; }
  .objective {
    left: 34px; top: 360px; width: 520px;
    font-size: 10px; line-height: 1.5; color: var(--ink);
  }
  .competency-list {
    list-style: none; font-size: 10.5px; color: var(--ink); line-height: 1.85;
  }
  .competency-list li { display: flex; align-items: center; gap: 10px; }
  .competency-list li::before {
    content: ""; width: 8px; height: 8px; border-radius: 50%;
    background: var(--cyan); flex: none;
  }
  .list-left { left: 34px; top: 392px; }
  .list-right { left: 320px; top: 392px; }
  .callout-band {
    left: 0; top: 520px; width: 600px; height: 120px;
    background: var(--cyan); color: var(--paper);
    padding: 16px 40px; text-align: center;
  }
  .callout-heading {
    font-family: "Montserrat", Arial, sans-serif;
    font-weight: 700; font-size: 14px; margin-bottom: 8px;
  }
  .callout-text { font-size: 10px; line-height: 1.5; }
  .web-tab { left: 0; top: 640px; width: 600px; height: 40px; }
  .web-link {
    right: 30px; top: 648px;
    font-size: 10.5px; color: var(--paper); text-decoration: underline;
  }
  .summary {
    left: 34px; top: 700px; width: 532px;
    font-size: 10px; line-height: 1.55; color: var(--ink);
  }
  .footer { left: 0; top: 780px; width: 600px; height: 70px; }
  .contact {
    left: 34px; top: 806px;
    font-size: 11px; color: var(--paper); text-decoration: underline;
  }
</style>
</head>
<body>
<article class="flyer">
  <svg class="hero-photo" viewBox="0 0 600 215" role="img" aria-label="Photo of a modern train station roof with light trails in blue and green">
    <defs>
      <linearGradient id="heroTone" x1="0" y1="0" x2="1" y2="1">
        <stop offset="0" stop-color="#2a6f9b"/>
        <stop offset=".45" stop-color="#5fc6e6"/>
        <stop offset=".7" stop-color="#7cc96a"/>
        <stop offset="1" stop-color="#dff2f8"/>
      </linearGradient>
    </defs>
    <polygon points="150,0 600,0 600,215 250,215" fill="url(#heroTone)"/>
  </svg>

  <div class="brand"><span class="brand-mark"></span>CORVANT</div>

  <svg class="title-panel" viewBox="0 0 360 140" aria-hidden="true">
    <polygon points="0,0 330,0 360,140 0,140" fill="var(--navy)"/>
  </svg>
  <div class="title-block">
    <h1 class="title">Train Driver<br>Competency Indicator<br>Development Project</h1>
    <p class="intro">We are commencing an applied research project to develop and test a framework of underlying core competencies for train driver performance.</p>
  </div>

  <svg class="texture" viewBox="0 0 250 150" role="img" aria-label="Soft light blue dotted background texture">
    <defs>
      <linearGradient id="textureTone" x1="0" y1="0" x2="1" y2="0">
        <stop offset="0" stop-color="#ffffff"/>
        <stop offset="1" stop-color="var(--cyan-light)"/>
      </linearGradient>
    </defs>
    <rect width="250" height="150" fill="url(#textureTone)"/>
  </svg>

  <p class="objective">The objective of the project is to identify observable indicators that describe effective performance in the following types of underlying competencies:</p>

  <ul class="competency-list list-left">
    <li>Application of Procedures</li>
    <li>Communication</li>
    <li>Operation of Tools / Equipment</li>
    <li>Problem Solving and Decision Making</li>
    <li>Route Knowledge</li>
    <li>Self Management</li>
  </ul>
  <ul class="competency-list list-right">
    <li>Situation Awareness</li>
    <li>System Knowledge</li>
    <li>Teamwork and Leadership</li>
    <li>Train Handling</li>
    <li>Workload Management</li>
  </ul>

  <section class="callout-band">
    <h2 class="callout-heading">Underlying competencies:</h2>
    <p class="callout-text">The underpinning knowledge and skills required by a train driver to perform a range of different tasks effectively. Underlying competencies include both ‘technical’ and ‘non-technical’ skills. They are not specific to one driving task, but help build resilient performance across all tasks, conditions or situations that a driver may encounter.</p>
  </section>

  <svg class="web-tab" viewBox="0 0 600 40" aria-hidden="true">
    <polygon points="0,0 600,0 600,40 0,40" fill="var(--paper)"/>
    <polygon points="300,0 600,0 600,40 340,40" fill="var(--cyan)"/>
    <polygon points="250,0 300,0 340,40 290,40" fill="var(--navy)"/>
  </svg>
  <a class="web-link" href="#">www.corvant.com.au</a>

  <p class="summary">In contrast to other performance marker systems, the current project aims to include both ‘technical’ and ‘non-technical’ skills in an integrated framework, with substantial input from drivers across the industry, both in passenger and freight operations. The aim is to develop a framework that uses a language that describes performance in a way that is relatable to drivers, trainers, and assessors.</p>

  <svg class="footer" viewBox="0 0 600 70" aria-hidden="true">
    <rect width="600" height="70" fill="var(--navy)"/>
    <polygon points="380,0 600,0 600,70 430,70" fill="var(--navy-deep)"/>
  </svg>
  <a class="contact" href="#">contact@corvant.com.au</a>
</article>
</body>
</html>
```